Brightline Energy Product Distribution Brochure

We are looking to have our current brochure for our customers completely redesigned...the idea is to present the relevant information in an attractive way . Our website is brightlineenergyco.example where you can find more information about us. We have included a file with a rough idea of the page order and what each should include but feel free to adapt based on design. The example provided is only for context and doesnt have to be maintained. We will be using the brochure both digitally and in print form. As long as it reads easily and is eye catching, the design can be horizontal or vertical.Final deliverable should be indesign file.

"Our Brands" page: should be limited to one page (space being enough) where it has the header for each one (for example diesel generators) space for one or two lines of text and then the corresponding logos for each of the five categories
Updates

For those asking: the "our brands" page should be a single page layout where there is a header with the corresponding section and space for maybe one line of text followed by the two logos for that category. Each of the product pages should be similar in fashion to the one in the document attached: a photo of the product with some white space and space for the text to be included. We will be posting additional examples today

Target Market(s)

We want to present it to customers both digitally and in print so they can see our products

Industry/Entity Type

Power Generation

Font styles to use
Serif

Requirements
Must have
• Eye catching and able to present the information in a presentable fashion. Rest is up to you.
Nice to have
• Should incorporate the colors of our logo but can also add other depending on design

```html
<!DOCTYPE html>
<html lang="en">
<head>
<meta charset="utf-8">
<title>Brightline Energy Brochure – Index &amp; About</title>
<link href="https://fonts.googleapis.com/css2?family=Roboto:ital,wght@0,400;0,700;1,300;1,700&display=swap" rel="stylesheet">
<style>
  :root {
    --bg: #f2f3f5;
    --paper: #ffffff;
    --yellow: #f7e11a;
    --orange: #f5a51c;
    --gold: #f5b21b;
    --charcoal: #58524f;
    --ink: #1e1e1e;
    --headline: #4a4646;
    --photo-dark: #2a2a2c;
    --photo-light: #d9dadc;
  }
  * { margin: 0; padding: 0; box-sizing: border-box; }
  html, body { width: 1200px; height: 1200px; overflow: hidden; background: var(--bg); }
  body { position: relative; font-family: "Roboto", Arial, sans-serif; }

  .spread {
    position: absolute; left: 112px; top: 286px;
    width: 978px; height: 630px;
    background: var(--paper);
    box-shadow: 4px 5px 6px rgba(0,0,0,0.35);
    overflow: hidden;
  }
  .spread-shapes { position: absolute; inset: 0; }

  .index-title {
    position: absolute; left: 34px; top: 36px;
    font-size: 31px; font-weight: 300; font-style: italic;
    letter-spacing: 2px; color: #fff;
  }
  .index-title .accent { color: var(--gold); margin-left: 6px; }

  .index-list { list-style: none; }
  .index-row {
    position: absolute; left: 58px; height: 14px;
    display: flex; align-items: center;
    font-size: 11.5px; font-weight: 700; white-space: nowrap;
  }
  .index-row .page { color: #fff; }
  .index-row .dots { color: #fff; letter-spacing: 1.6px; overflow: hidden; }
  .index-row .section { color: var(--gold); position: absolute; }

  .about-title {
    position: absolute; left: 511px; top: 82px;
    font-size: 30px; font-weight: 300; font-style: italic;
    color: var(--headline); white-space: nowrap; letter-spacing: -0.3px;
  }
  .about-title .accent { color: var(--gold); }

  .about-body {
    position: absolute; left: 511px; top: 146px; width: 172px;
    font-size: 9.4px; line-height: 12.8px; color: var(--ink);
  }

  .team-photo {
    position: absolute; left: 511px; top: 392px; width: 444px; height: 238px;
    border: 2px solid #fff; border-bottom: none;
    background: linear-gradient(90deg, var(--photo-light) 0%, #c9cacc 45%, var(--photo-dark) 65%, #1c1c1e 100%);
  }
  .team-photo .page-tag {
    position: absolute; right: 6px; bottom: 10px;
    font-size: 10.5px; font-weight: 700; font-style: italic; color: #fff; letter-spacing: 0.5px;
  }
</style>
</head>
<body>
  <section class="spread">
    <svg class="spread-shapes" width="978" height="630" viewBox="0 0 978 630" aria-hidden="true">
      <defs>
        <linearGradient id="sunband" x1="0" y1="0" x2="0.6" y2="1">
          <stop offset="0" stop-color="#f6a41b"/>
          <stop offset="0.35" stop-color="#f9d21a"/>
          <stop offset="1" stop-color="#f7e41a"/>
        </linearGradient>
        <linearGradient id="steel" x1="0" y1="0" x2="1" y2="1">
          <stop offset="0" stop-color="#4f4a48"/>
          <stop offset="1" stop-color="#5d5755"/>
        </linearGradient>
      </defs>
      <polygon points="0,0 92,0 390,630 0,630" fill="url(#sunband)"/>
      <polygon points="638,0 978,0 978,630 964,630" fill="url(#steel)"/>
      <polygon points="622,0 631,0 839,390 830,390" fill="#4e4947"/>
    </svg>

    <h1 class="index-title">INDE<span class="accent">X</span></h1>

    <ul class="index-list">
      <li class="index-row" style="top:107px"><span class="page">PAGE 3</span><span class="dots">&nbsp;.&nbsp;.&nbsp;.&nbsp;.&nbsp;.</span><span class="section" style="left:91px">ABOUT OUR COMPANY</span></li>
      <li class="index-row" style="top:139px"><span class="page">PAGE 4</span><span class="dots">&nbsp;.&nbsp;.&nbsp;.&nbsp;.&nbsp;.&nbsp;.&nbsp;.&nbsp;.</span><span class="section" style="left:106px">OUR BRANDS</span></li>
      <li class="index-row" style="top:171px"><span class="page">PAGE 5</span><span class="dots">&nbsp;.&nbsp;.&nbsp;.&nbsp;.&nbsp;.&nbsp;.&nbsp;.&nbsp;.&nbsp;.&nbsp;.</span><span class="section" style="left:121px">OUR STOCK</span></li>
      <li class="index-row" style="top:203px"><span class="page">PAGE 6</span><span class="dots">&nbsp;.&nbsp;.&nbsp;.&nbsp;.&nbsp;.&nbsp;.&nbsp;.&nbsp;.&nbsp;.&nbsp;.&nbsp;.&nbsp;.</span><span class="section" style="left:136px">STANDBY GENERATORS</span></li>
      <li class="index-row" style="top:235px"><span class="page">PAGE 7</span><span class="dots">&nbsp;.&nbsp;.&nbsp;.&nbsp;.&nbsp;.&nbsp;.&nbsp;.&nbsp;.&nbsp;.&nbsp;.&nbsp;.&nbsp;.&nbsp;.&nbsp;.</span><span class="section" style="left:152px">PRIME GENERATORS</span></li>
      <li class="index-row" style="top:267px"><span class="page">PAGE 8</span><span class="dots">&nbsp;.&nbsp;.&nbsp;.&nbsp;.&nbsp;.&nbsp;.&nbsp;.&nbsp;.&nbsp;.&nbsp;.&nbsp;.&nbsp;.&nbsp;.&nbsp;.&nbsp;.&nbsp;.</span><span class="section" style="left:167px">RENTAL GENERATORS</span></li>
      <li class="index-row" style="top:299px"><span class="page">PAGE 9</span><span class="dots">&nbsp;.&nbsp;.&nbsp;.&nbsp;.&nbsp;.&nbsp;.&nbsp;.&nbsp;.&nbsp;.&nbsp;.&nbsp;.&nbsp;.&nbsp;.&nbsp;.&nbsp;.&nbsp;.&nbsp;.&nbsp;.</span><span class="section" style="left:182px">AC ALTERNATORS</span></li>
      <li class="index-row" style="top:331px"><span class="page">PAGE 10</span><span class="dots">&nbsp;.&nbsp;.&nbsp;.&nbsp;.&nbsp;.&nbsp;.&nbsp;.&nbsp;.&nbsp;.&nbsp;.&nbsp;.&nbsp;.&nbsp;.&nbsp;.&nbsp;.&nbsp;.&nbsp;.&nbsp;.</span><span class="section" style="left:198px">ALTERNATOR PARTS</span></li>
      <li class="index-row" style="top:363px"><span class="page">PAGE 11</span><span class="dots">&nbsp;.&nbsp;.&nbsp;.&nbsp;.&nbsp;.&nbsp;.&nbsp;.&nbsp;.&nbsp;.&nbsp;.&nbsp;.&nbsp;.&nbsp;.&nbsp;.&nbsp;.&nbsp;.&nbsp;.&nbsp;.&nbsp;.&nbsp;.</span><span class="section" style="left:213px">CONTROLLERS</span></li>
      <li class="index-row" style="top:395px"><span class="page">PAGE 12</span><span class="dots">&nbsp;.&nbsp;.&nbsp;.&nbsp;.&nbsp;.&nbsp;.&nbsp;.&nbsp;.&nbsp;.&nbsp;.&nbsp;.&nbsp;.&nbsp;.&nbsp;.&nbsp;.&nbsp;.&nbsp;.&nbsp;.&nbsp;.&nbsp;.&nbsp;.&nbsp;.</span><span class="section" style="left:228px">TRANSFER SWITCHES</span></li>
      <li class="index-row" style="top:427px"><span class="page">PAGE 13</span><span class="dots">&nbsp;.&nbsp;.&nbsp;.&nbsp;.&nbsp;.&nbsp;.&nbsp;.&nbsp;.&nbsp;.&nbsp;.&nbsp;.&nbsp;.&nbsp;.&nbsp;.&nbsp;.&nbsp;.&nbsp;.&nbsp;.&nbsp;.&nbsp;.&nbsp;.&nbsp;.&nbsp;.&nbsp;.</span><span class="section" style="left:243px">OUR DISTRIBUTORS</span></li>
    </ul>

    <h2 class="about-title">ABOUT OUR <span class="accent">COMPANY</span></h2>

    <p class="about-body">
      Not all customer needs are the same and being able to accommodate to the specifications of each can become challenging. Brightline Energy has the experience necessary to take on major special projects with a quick turn-around.<br>
      We understand the specifific requirements of each industry and market. Our team of experts are capable modify and customized our products to fit your needs.<br>
      Let us worry about the complexities of manufacturing and engineering while you exploit the opportunity for your clients.
    </p>

    <div class="team-photo" role="img" aria-label="Photo of three team members in black shirts standing beside an open diesel generator set in a white showroom">
      <span class="page-tag">PAGE 3</span>
    </div>
  </section>
</body>
</html>
```